Brovanek Data Yellow rose letterhead

I have a new logo for my company but in its current form it is too large to be used on letterhead or as a email signature. I need to have the designer use elements from the current logo and create something close to the original but more suited for smaller items.
Updates

I just uploaded a copy of our logo that does not have the weathered affect. Thanks

Reason: More time for revisions

Industry/Entity Type

It Company

Requirements
Must have
• The design must maintain the visual effect of the current logo. It needs to include the yellow rose and the name of the company.
Nice to have
• It would be nice to maintain the stamp theme and incorporate my name, address, phone, email. etc.

```html
<!DOCTYPE html>
<html lang="en">
<head>
<meta charset="utf-8">
<title>Brovanek Data Letterhead</title>
<link href="https://fonts.googleapis.com/css2?family=Baloo+2:wght@500;600;700&display=swap" rel="stylesheet">
<style>
  :root {
    --gold: #ffc914;
    --gold-soft: #fde9a0;
    --cream: #fdf3cc;
    --paper: #ffffff;
    --teal: #3bb8be;
    --ink: #5b4a44;
  }
  html, body {
    margin: 0;
    padding: 0;
    width: 929px;
    height: 1200px;
    overflow: hidden;
    background: var(--paper);
  }
  .letterhead {
    position: relative;
    width: 929px;
    height: 1200px;
    overflow: hidden;
    background: var(--paper);
    font-family: "Baloo 2", sans-serif;
    color: var(--ink);
  }
  .band {
    position: absolute;
    left: 0;
    width: 929px;
  }
  .band--top {
    top: 0;
    height: 103px;
    background: linear-gradient(90deg,
      var(--gold) 0%, var(--gold) 14%,
      var(--gold-soft) 28%, var(--cream) 50%,
      var(--gold-soft) 68%, var(--gold) 80%, var(--gold) 100%);
  }
  .band--bottom {
    bottom: 0;
    height: 106px;
    background: linear-gradient(90deg,
      var(--gold) 0%, var(--gold) 6%,
      var(--gold-soft) 22%, var(--cream) 48%,
      var(--gold-soft) 72%, var(--gold) 86%, var(--gold) 100%);
  }
  .rose-art {
    position: absolute;
    top: 44px;
    left: 728px;
    width: 190px;
    height: 180px;
    border-radius: 50%;
    background: radial-gradient(circle at 45% 40%, #fff1a8 0%, #ffd84a 45%, var(--gold) 100%);
  }
  .brand {
    position: absolute;
    top: 232px;
    left: 704px;
    width: 220px;
    text-align: center;
  }
  .brand__name {
    margin: 0;
    font-size: 23px;
    font-weight: 600;
    line-height: 24px;
    color: var(--teal);
  }
  .brand__tagline {
    margin: 2px 0 0;
    font-size: 15px;
    font-weight: 700;
    line-height: 18px;
  }
  .brand__motto {
    margin: 4px auto 0;
    padding-top: 3px;
    width: 200px;
    border-top: 1px solid var(--ink);
    font-size: 11.5px;
    font-weight: 700;
    line-height: 13px;
  }
  .contact {
    position: absolute;
    top: 446px;
    left: 23px;
    margin: 0;
    font-style: normal;
    font-size: 14px;
    font-weight: 600;
    line-height: 27.5px;
  }
  .contact span { display: block; }
</style>
</head>
<body>
  <main class="letterhead">
    <div class="band band--top"></div>

    <div class="rose-art" role="img" aria-label="Illustration of a yellow rose in full bloom"></div>

    <header class="brand">
      <p class="brand__name">Brovanek Data</p>
      <p class="brand__tagline">Insight Built to Order</p>
      <p class="brand__motto">Careful Research for Every<br>Growing Business</p>
    </header>

    <address class="contact">
      <span class="contact__name">Mara Quillen, PhD</span>
      <span class="contact__street">218 W Pecan Hollow Rd, Ste 410</span>
      <span class="contact__city">Cedar Bluff, TX 76510</span>
      <span class="contact__email">mara@brovanek-data.com</span>
      <span class="contact__phone">1-800-555-0147</span>
    </address>

    <div class="band band--bottom"></div>
  </main>
</body>
</html>
```